Business card design for holistic health care clinic

We need a double-sided business card design for our holistic health care clinic that integrates our logo design and also its color scheme. My business is called Valmira. It is an integrative medicine clinic. You have already done the logo for me. Please ensure an elegant and upscale design that is not cluttered, but still has all the necessary information (please see below for details).

Target Market(s)

Wellness, fitness, rehabilitation for educated, well-traveled open-minded clients who are focused on natural, organic, balanced and preventive healthcare and lifestyle.

Industry/Entity Type

Medical

Contact Information for Business Card

Modern, clean.

Number of Pages Required

1 page

Font styles to use
Serif
Sans Serif

Colors

Designer to choose colors to be used in the design.

Requirements
Must have
• Logo on one side, all other information on the other side.
• Other information should include:
• Tobias Wrenfeld - DOE, CPT, LMT
• 4100 East Marrow Drive
• Austin, TX 78119
• 512 555 0148
• 818 555 0192
• info@ValmiraHealth.example
• t.wrenfeld@ValmiraHealth.example
Nice to have
• Darker background on front - but not totally black - shaded/dark gray.

```html
<!DOCTYPE html>
<html lang="en">
<head>
<meta charset="utf-8">
<title>Valmira Business Card</title>
<link rel="stylesheet" href="https://fonts.googleapis.com/css2?family=Nunito:wght@800&family=Roboto:wght@400;700&family=Roboto+Condensed:wght@700&display=swap">
<style>
  :root {
    --backdrop: #d6a77a;
    --card-dark: #2a2a2a;
    --card-light: #f4f4f4;
    --brand-blue: #0a8fcb;
    --ink-dark: #222222;
    --ink-light: #ffffff;
    --ink-muted: #555555;
  }
  * { margin: 0; padding: 0; box-sizing: border-box; }
  html, body { width: 1200px; height: 960px; overflow: hidden; }
  body { background: var(--backdrop); position: relative; font-family: "Roboto", sans-serif; }

  .card { position: absolute; width: 600px; height: 344px; box-shadow: 0 2px 4px rgba(0,0,0,0.35); }
  .card--front { left: 314px; top: 113px; background: linear-gradient(180deg, #2e2e2e, var(--card-dark)); }
  .card--back { left: 311px; top: 472px; background: var(--card-light); }

  .brand { position: absolute; text-align: center; color: var(--brand-blue); }
  .brand__name { font-family: "Nunito", sans-serif; font-weight: 800; letter-spacing: 1px; line-height: 1; }
  .brand__tagline { font-family: "Nunito", sans-serif; font-weight: 800; }

  .card--front .brand { left: 300px; top: 84px; width: 276px; }
  .card--front .brand__name { font-size: 52px; }
  .card--front .brand__tagline { font-size: 15px; margin-top: 8px; }

  .name-band { position: absolute; left: 0; top: 210px; width: 201px; height: 48px; background: var(--brand-blue); }
  .name-band__stripe-white { position: absolute; left: 202px; top: 210px; width: 4px; height: 48px; background: var(--ink-light); }
  .name-band__stripe-blue { position: absolute; left: 209px; top: 210px; width: 6px; height: 48px; background: var(--brand-blue); }
  .person { position: absolute; left: 36px; top: 217px; color: var(--ink-dark); }
  .person__name { font-family: "Roboto Condensed", sans-serif; font-weight: 700; font-size: 20px; line-height: 22px; text-transform: uppercase; }
  .person__credentials { font-family: "Roboto Condensed", sans-serif; font-weight: 700; font-size: 11px; line-height: 13px; }

  .address { position: absolute; left: 33px; top: 266px; color: var(--ink-light); font-size: 15px; line-height: 19px; }

  .contact { position: absolute; right: 45px; top: 220px; text-align: right; color: var(--ink-light); font-size: 15px; line-height: 19px; }
  .contact__label { color: var(--brand-blue); font-weight: 700; }
  .contact__web { margin-top: 8px; }
  .accent-bar { position: absolute; right: 1px; top: 221px; width: 8px; height: 80px; background: var(--brand-blue); }

  .card--back .brand { left: 0; width: 600px; top: 145px; }
  .card--back .brand__name { font-size: 60px; }
  .card--back .brand__tagline { font-size: 17px; margin-top: 10px; }
  .slogan { position: absolute; left: 0; width: 600px; top: 291px; text-align: center; color: var(--ink-muted); font-size: 14px; }
</style>
</head>
<body>
  <section class="card card--front">
    <div class="brand">
      <div class="brand__name">VALMIRA</div>
      <div class="brand__tagline">Integrative Holistic Medicine</div>
    </div>
    <div class="name-band"></div>
    <div class="name-band__stripe-white"></div>
    <div class="name-band__stripe-blue"></div>
    <div class="person">
      <div class="person__name">Tobias Wrenfeld</div>
      <div class="person__credentials">DOE, CPT, LMT</div>
    </div>
    <div class="address">
      <div>4100 East Marrow Drive</div>
      <div>Austin, TX 78119</div>
    </div>
    <div class="contact">
      <div><span class="contact__label">P:</span> 512 555 0148</div>
      <div><span class="contact__label">C:</span> 818 555 0192</div>
      <div class="contact__web">t.wrenfeld@ValmiraHealth.example</div>
      <div>www.ValmiraHealth.example</div>
    </div>
    <div class="accent-bar"></div>
  </section>

  <section class="card card--back">
    <div class="brand">
      <div class="brand__name">VALMIRA</div>
      <div class="brand__tagline">Integrative Holistic Medicine</div>
    </div>
    <p class="slogan">it’s all about you — your health, your objectives</p>
  </section>
</body>
</html>
```